I need a flyer made , the flyer can be one page or two pages or three pages . I will be posting this on Instagram and social media platforms. I am a luxury home builder , I am looking to hire a construction project manager . Below are some examples and ideas what can be on the flyer

We’re looking for a construction project manager who’s passionate about building luxury homes at the highest standards
We’re hiring construction project manager
* Experience 5+ years in residential project management with a strong portfolio of completed homes.
* location : Bergen County NJ
* excellent leadership skills, leads teams with confidence and clarity
* communicates seamlessly with architects , engineers, designers and clients
*knows how to manage budgets and timelines without compromising quality
*solves problems with a positive solution first mindset
* pays attention to every detail because in luxury the small things are the big things

Apply now , link in bio or DM to connect.

My logo is attached, my web site www.velstridebuilders.com
My style is modern but still warm and inviting. I like a clean classy look .

Please don’t add any images of chairs or people to the flyer , I do not want people on my flyer. Do not add standard images of offices and houses , we are luxury builders , we build homes over 2 million dollars. Keep a classy , simple modern look . High end .

You can add a white hard hat with my logo on it for a image , this is a suggestion does not have to be on my flyer ,

```html
<!DOCTYPE html>
<html lang="en">
<head>
<meta charset="utf-8">
<title>Velstride Builders – Hiring Construction Project Manager</title>
<link href="https://fonts.googleapis.com/css2?family=Great+Vibes&family=Poppins:wght@400;500;600;700;800&display=swap" rel="stylesheet">
<style>
  :root{
    --cream:#f2ece3;
    --cream-light:#faf7f2;
    --cream-shade:#e4dccf;
    --ink:#1f1f1f;
    --ink-soft:#2b2b2b;
    --slate:#4f4f4f;
    --slate-light:#5e5e5e;
    --white:#ffffff;
    --hat-white:#f7f5f1;
    --hat-shade:#d6d0c6;
  }
  *{margin:0;padding:0;box-sizing:border-box}
  html,body{width:1200px;height:1200px;overflow:hidden}
  body{font-family:"Poppins",sans-serif;color:var(--ink);background:var(--cream)}
  .flyer{
    position:relative;width:1200px;height:1200px;overflow:hidden;
    background:
      radial-gradient(ellipse 700px 300px at 80% 20%, var(--cream-light), transparent 70%),
      linear-gradient(160deg, var(--cream-light) 0%, var(--cream) 45%, var(--cream-shade) 100%);
  }
  .architecture-sketch{
    position:absolute;left:0;top:27px;width:505px;height:620px;
    background:linear-gradient(180deg, rgba(200,193,182,.28), rgba(200,193,182,.04));
    border-radius:4px;
  }
  .feature-image{
    position:absolute;left:262px;top:120px;width:222px;height:440px;
    background:radial-gradient(ellipse at 50% 40%, var(--hat-white), var(--hat-shade) 80%);
    border-radius:24px;
  }
  .location-pin{position:absolute;left:122px;top:306px;width:160px;height:254px}
  .location-pin .pin-label{
    position:absolute;left:36px;top:38px;width:88px;height:88px;
    display:flex;align-items:center;justify-content:center;text-align:center;
    font-weight:600;font-size:16px;line-height:1.2;color:var(--ink);
  }
  .megaphone{
    position:absolute;left:830px;top:90px;width:120px;height:130px;
    background:radial-gradient(circle at 40% 40%,#b5b5b5,#5a5a5a);
    border-radius:40%;opacity:.8;
  }
  .headline-script{
    position:absolute;left:505px;top:150px;
    font-family:"Great Vibes",cursive;font-size:118px;line-height:1;color:var(--ink);
  }
  .headline-main{
    position:absolute;left:500px;top:240px;
    font-weight:700;font-size:160px;letter-spacing:5px;line-height:1;color:var(--ink-soft);
  }
  .role-title{position:absolute;left:502px;top:410px;line-height:1;color:var(--ink-soft)}
  .role-title .line-one{display:block;font-weight:700;font-size:51px;letter-spacing:-.5px}
  .role-title .line-two{display:block;font-weight:400;font-size:44px;margin-top:4px;letter-spacing:-1px}
  .role-title .line-two strong{font-weight:700}
  .tagline-pills{position:absolute;left:500px;top:524px;display:flex;height:46px}
  .tagline-pills span{
    display:flex;align-items:center;padding:0 22px;font-size:20px;color:var(--white);font-weight:400;
  }
  .tagline-pills strong{font-weight:700;margin-left:6px}
  .tagline-pills .pill-left{background:var(--ink-soft);border-radius:23px 0 0 23px;width:204px}
  .tagline-pills .pill-right{background:var(--slate);border-radius:0 23px 23px 0;margin-left:3px;width:207px}
  .requirements{
    position:absolute;left:75px;top:651px;width:1050px;height:290px;
    display:flex;border-radius:22px;overflow:hidden;box-shadow:0 8px 20px rgba(0,0,0,.15);
  }
  .requirements ul{list-style:none;padding-top:38px;color:var(--white)}
  .requirements .column-left{width:525px;padding-left:52px;background:var(--ink-soft)}
  .requirements .column-right{width:525px;padding-left:31px;background:linear-gradient(90deg,var(--slate),var(--slate-light))}
  .requirements li{
    position:relative;padding-left:17px;font-size:19.5px;line-height:24.5px;margin-bottom:15px;max-width:420px;
  }
  .requirements li strong{font-weight:700}
  .requirements li svg{position:absolute;left:-17px;top:5px;width:15px;height:15px}
  .brand-name{position:absolute;left:68px;top:1024px;width:325px;text-align:center;color:var(--ink);font-weight:500;line-height:1}
  .brand-name .brand-top{display:block;font-size:52px;letter-spacing:3px}
  .brand-name .brand-bottom{display:block;font-size:27px;letter-spacing:8px;margin-top:12px}
  .cta{position:absolute;left:431px;top:1008px;display:flex;height:50px}
  .cta .apply-button{
    background:linear-gradient(180deg,#3a3a3a,#111);color:var(--white);font-weight:700;font-size:24px;
    border-radius:25px;padding:0 34px;display:flex;align-items:center;width:206px;z-index:1;
  }
  .cta .connect-note{
    background:var(--white);border:1.5px solid #9a9a9a;border-radius:25px;margin-left:-4px;
    font-weight:600;font-size:23px;display:flex;align-items:center;justify-content:center;width:418px;
  }
  .socials{position:absolute;left:431px;top:1074px;font-size:18px}
  .socials h3,.website h3{font-weight:700;font-size:20px;margin-bottom:2px}
  .socials .handles{display:flex;gap:14px}
  .socials .handle{display:flex;align-items:center;gap:5px}
  .socials .dot{width:13px;height:13px;border-radius:50%;background:var(--ink-soft)}
  .divider{position:absolute;left:822px;top:1078px;width:1.5px;height:52px;background:var(--ink)}
  .website{position:absolute;left:834px;top:1074px;font-size:18px}
</style>
</head>
<body>
<main class="flyer">
  <div class="architecture-sketch" role="img" aria-label="Faint line sketch of modern luxury architecture"></div>
  <div class="feature-image" role="img" aria-label="White hard hat with the builder's name"></div>

  <div class="location-pin">
    <svg viewBox="0 0 160 254" width="160" height="254" aria-hidden="true">
      <defs>
        <linearGradient id="pinFill" x1="0" y1="0" x2="1" y2="1">
          <stop offset="0" stop-color="#f03a32"/><stop offset="1" stop-color="#b01414"/>
        </linearGradient>
      </defs>
      <path d="M80 2 C36 2 4 36 4 80 C4 140 80 250 80 250 C80 250 156 140 156 80 C156 36 124 2 80 2 Z" fill="url(#pinFill)"/>
      <circle cx="80" cy="82" r="46" fill="#ffffff"/>
    </svg>
    <div class="pin-label">Bergen<br>County,<br>NJ</div>
  </div>

  <div class="megaphone" role="img" aria-label="Silver megaphone"></div>

  <div class="headline-script">We’re</div>
  <h1 class="headline-main">HIRING</h1>
  <h2 class="role-title">
    <span class="line-one">CONSTRUCTION</span>
    <span class="line-two">PROJECT <strong>MANAGER</strong></span>
  </h2>
  <div class="tagline-pills">
    <span class="pill-left">BUILD<strong>LUXURY</strong></span>
    <span class="pill-right">LEAD<strong>EXCELLENCE</strong></span>
  </div>

  <section class="requirements">
    <ul class="column-left">
      <li><svg viewBox="0 0 16 16"><circle cx="8" cy="8" r="8" fill="#d8d8d8"/><path d="M4.5 8.2l2.3 2.3 4.7-4.7" stroke="#2b2b2b" stroke-width="1.8" fill="none"/></svg>Experience <strong>5+ years</strong> in residential project management with a strong portfolio of completed homes.</li>
      <li><svg viewBox="0 0 16 16"><circle cx="8" cy="8" r="8" fill="#d8d8d8"/><path d="M4.5 8.2l2.3 2.3 4.7-4.7" stroke="#2b2b2b" stroke-width="1.8" fill="none"/></svg>Excellent <strong>leadership skills,</strong> leads teams with confidence and clarity</li>
      <li><svg viewBox="0 0 16 16"><circle cx="8" cy="8" r="8" fill="#d8d8d8"/><path d="M4.5 8.2l2.3 2.3 4.7-4.7" stroke="#2b2b2b" stroke-width="1.8" fill="none"/></svg><strong>Communicates seamlessly</strong> with architects , engineers, designers and clients</li>
    </ul>
    <ul class="column-right">
      <li><svg viewBox="0 0 16 16"><circle cx="8" cy="8" r="8" fill="#d8d8d8"/><path d="M4.5 8.2l2.3 2.3 4.7-4.7" stroke="#4f4f4f" stroke-width="1.8" fill="none"/></svg>Knows how to <strong>manage budgets and timelines</strong> without compromising quality</li>
      <li><svg viewBox="0 0 16 16"><circle cx="8" cy="8" r="8" fill="#d8d8d8"/><path d="M4.5 8.2l2.3 2.3 4.7-4.7" stroke="#4f4f4f" stroke-width="1.8" fill="none"/></svg><strong>Solves problems</strong> with a positive solution first mindset</li>
      <li><svg viewBox="0 0 16 16"><circle cx="8" cy="8" r="8" fill="#d8d8d8"/><path d="M4.5 8.2l2.3 2.3 4.7-4.7" stroke="#4f4f4f" stroke-width="1.8" fill="none"/></svg><strong>Pays attention to every detail</strong> because in luxury the small things are the big things</li>
    </ul>
  </section>

  <div class="brand-name">
    <span class="brand-top">VELSTRIDE</span>
    <span class="brand-bottom">builders</span>
  </div>

  <div class="cta">
    <span class="apply-button">Apply now</span>
    <span class="connect-note">Link in bio or DM to connect</span>
  </div>

  <div class="socials">
    <h3>Follow us</h3>
    <div class="handles">
      <span class="handle"><span class="dot"></span>velstridebuilders</span>
      <span class="handle"><span class="dot"></span>VelstrideBldrs</span>
    </div>
  </div>
  <div class="divider"></div>
  <div class="website">
    <h3>Visit us</h3>
    <span>www.velstridebuilders.com</span>
  </div>
</main>
</body>
</html>
```